Business Card Design For Marketing Agnecy LVP

Need business card design for marketing agency.

Doug Fenwick
President, CEO
1-555-302-4196
doug@boldpromoperksgroup.example
www.BoldPromoPerksGroup.example

Back Side:
Boost Sales Using Rewards, Incentives & Giveaways
Get A Free Sample Package

Target Market(s)

B2B

Industry/Entity Type

Marketing

Contact Information for Business Card

Doug Fenwick
President, CEO
1-555-302-4196

Back Side:
Get A Free Sample Package

Please note that my current url is OLD DESIGN. I am working on new design and want the business card to match color themes at least on new site. Here is the demo link for new site so you can see the colors I use, etc.

http://layoutcratehub.example/kq/doug/lvp_final/index.html

Requirements
Must have
• Please note that my current url is OLD DESIGN. I am working on new design and want the business card to match color themes at least on new site. Here is the demo link for new site so you can see the colors I use, etc.

Nice to have

Should not have

```html
<!DOCTYPE html>
<html lang="en">
<head>
<meta charset="utf-8">
<title>LVP – Business Card</title>
<link rel="stylesheet" href="https://fonts.googleapis.com/css2?family=Open+Sans:wght@400;600;700&display=swap">
<style>
  :root {
    --brand-blue: #2f7bbf;
    --ink-gray: #5f6062;
    --paper: #ffffff;
  }
  * { margin: 0; padding: 0; box-sizing: border-box; }
  html, body {
    width: 1200px;
    height: 750px;
    overflow: hidden;
    background: var(--paper);
    font-family: "Open Sans", Arial, sans-serif;
  }
  .card {
    position: relative;
    width: 1200px;
    height: 750px;
    background: var(--paper);
    overflow: hidden;
  }
  .identity {
    position: absolute;
    top: 64px;
    right: 64px;
    text-align: center;
  }
  .identity__name {
    font-size: 44px;
    line-height: 1.1;
    letter-spacing: 0.5px;
    color: var(--brand-blue);
    font-weight: 400;
  }
  .identity__surname {
    color: var(--ink-gray);
    font-weight: 700;
  }
  .identity__title {
    font-size: 30px;
    color: var(--ink-gray);
    line-height: 1.2;
  }
  .brand {
    position: absolute;
    left: 151px;
    top: 286px;
    width: 313px;
    color: var(--brand-blue);
    font-weight: 700;
    text-align: center;
  }
  .brand__mark {
    font-size: 150px;
    line-height: 1;
    letter-spacing: -2px;
  }
  .brand__name {
    margin-top: 14px;
    font-size: 21px;
    letter-spacing: 2px;
    white-space: nowrap;
  }
  .divider {
    position: absolute;
    left: 564px;
    top: 223px;
    width: 5px;
    height: 339px;
    border-radius: 3px;
    background: var(--brand-blue);
  }
  .contacts {
    position: absolute;
    left: 587px;
    top: 240px;
    list-style: none;
  }
  .contact {
    display: flex;
    align-items: center;
    height: 58px;
    margin-bottom: 52px;
    font-size: 27px;
    color: var(--ink-gray);
    white-space: nowrap;
  }
  .contact__icon {
    flex: none;
    width: 58px;
    height: 58px;
    margin-right: 15px;
  }
  .footer-band {
    position: absolute;
    left: 0;
    bottom: 0;
    width: 1200px;
    height: 58px;
  }
</style>
</head>
<body>
<main class="card">
  <header class="identity">
    <h1 class="identity__name">DOUG <span class="identity__surname">FENWICK</span></h1>
    <p class="identity__title">President, CEO</p>
  </header>

  <div class="brand" aria-label="LVP – Bold Promo Perks Group">
    <div class="brand__mark">LVP</div>
    <div class="brand__name">BOLD PROMO PERKS GROUP</div>
  </div>

  <div class="divider"></div>

  <ul class="contacts">
    <li class="contact">
      <svg class="contact__icon" viewBox="0 0 58 58" aria-hidden="true">
        <circle cx="29" cy="29" r="29" fill="var(--ink-gray)"/>
        <path d="M20 17c1.5-1.2 3-1 4 .5l2.5 4c.8 1.3.5 2.6-.7 3.5l-1.5 1.1c1 2.6 3.2 5 5.8 6.3l1.2-1.4c1-1.1 2.3-1.3 3.5-.5l4 2.6c1.4 1 1.6 2.5.4 4l-1.7 2c-1.6 1.8-4.5 2-8 .2-5.5-2.8-10-7.6-12.2-13-1.4-3.5-1-6.2.7-7.6z" fill="#fff"/>
        <path d="M31 18a9 9 0 0 1 9 9M31 13a14 14 0 0 1 14 14" stroke="#fff" stroke-width="2.2" fill="none" stroke-linecap="round"/>
      </svg>
      <span>1-555-302-4196</span>
    </li>
    <li class="contact">
      <svg class="contact__icon" viewBox="0 0 58 58" aria-hidden="true">
        <circle cx="29" cy="29" r="29" fill="var(--ink-gray)"/>
        <rect x="15" y="20" width="28" height="19" rx="1.5" fill="none" stroke="#fff" stroke-width="2.4"/>
        <path d="M15.5 21 29 31l13.5-10" fill="none" stroke="#fff" stroke-width="2.4" stroke-linejoin="round"/>
      </svg>
      <span>doug@boldpromoperksgroup.example</span>
    </li>
    <li class="contact">
      <svg class="contact__icon" viewBox="0 0 58 58" aria-hidden="true">
        <circle cx="29" cy="29" r="29" fill="var(--ink-gray)"/>
        <g fill="none" stroke="#fff" stroke-width="2">
          <circle cx="29" cy="29" r="15"/>
          <ellipse cx="29" cy="29" rx="6.5" ry="15"/>
          <path d="M29 14v30M14 29h30M16.5 21.5h25M16.5 36.5h25"/>
        </g>
      </svg>
      <span>www.BoldPromoPerksGroup.example</span>
    </li>
  </ul>

  <svg class="footer-band" viewBox="0 0 1200 58" aria-hidden="true">
    <polygon points="144,58 369,0 1200,0 1200,58" fill="var(--brand-blue)"/>
  </svg>
</main>
</body>
</html>
```